New Business Card Design Project

Use the flyer uploaded and website www.brightoakbuilders.com for inspiration.
List Our Services on Backside of business cards
Marcus Delling
Harborline Builders Inc.
Licensed General Contractors
858-471-6093

Contact Information for Business Card

Use the flyer uploaded and website www.brightoakbuilders.com for inspiration. List Our Services on Backside of business cards Marcus Delling Harborline Builders Inc. Licensed General Contractors 858-471-6093

```html
<!DOCTYPE html>
<html lang="en">
<head>
<meta charset="utf-8">
<title>Harborline Builders – Business Card</title>
<link href="https://fonts.googleapis.com/css2?family=Marcellus&family=Playfair+Display:wght@700&family=Arimo:wght@400&display=swap" rel="stylesheet">
<style>
  :root{
    --bg:#111111;
    --card:#2a2a2a;
    --card-edge:#333333;
    --ink:#ffffff;
    --muted:#cfcfcf;
    --faint:#3a3a3a;
    --rule:#8a8a8a;
  }
  *{box-sizing:border-box;margin:0;padding:0}
  html,body{width:1200px;height:963px;overflow:hidden;background:var(--bg)}
  .canvas{position:relative;width:1200px;height:963px;background:var(--bg)}
  .card{
    position:absolute;left:220px;width:760px;height:434px;
    background:var(--card);border-radius:22px;overflow:hidden;
    border:1px solid var(--card-edge);
    color:var(--ink);
  }
  .card--front{top:32px}
  .card--back{top:497px}

  .brand-name{
    font-family:"Marcellus",serif;font-size:34px;letter-spacing:2px;
    color:var(--ink);text-transform:uppercase;white-space:nowrap;
  }

  /* front */
  .card--front .brand-name{position:absolute;left:58px;top:64px}
  .palm-decoration{
    position:absolute;right:90px;bottom:0;width:300px;height:300px;
    background:radial-gradient(ellipse at 50% 45%, var(--faint) 0%, rgba(58,58,58,0) 70%);
  }
  .contact{position:absolute;left:58px;bottom:58px;font-family:"Arimo",sans-serif;font-size:22px}
  .contact-row{display:flex;align-items:center;gap:14px;margin-top:12px}
  .contact-row svg{width:22px;height:22px;flex:none}
  .person{position:absolute;right:62px;top:170px;text-align:right}
  .person-name{font-family:"Playfair Display",serif;font-weight:700;font-size:36px;letter-spacing:1px;text-transform:uppercase}
  .person-title{font-family:"Arimo",sans-serif;font-size:22px;margin-top:6px;color:var(--muted)}
  .edge-tab{position:absolute;right:0;top:178px;width:26px;height:50px;background:var(--ink)}

  /* back */
  .card--back .brand-name{position:absolute;left:44px;top:190px;font-size:30px}
  .divider{position:absolute;left:370px;top:50px;width:1px;height:334px;background:var(--rule)}
  .services{position:absolute;left:400px;top:54px}
  .services-title{font-family:"Marcellus",serif;font-size:36px;letter-spacing:1px;text-transform:uppercase;margin-bottom:14px}
  .service-list{list-style:none;font-family:"Arimo",sans-serif;font-size:19px;line-height:1.42}
  .service-list li{display:flex;align-items:center;gap:10px;white-space:nowrap}
  .service-list svg{width:17px;height:17px;flex:none}
</style>
</head>
<body>
<div class="canvas">

  <section class="card card--front">
    <div class="brand-name">Harborline Builders</div>
    <div class="palm-decoration" role="img" aria-label="Faint decorative palm tree graphic"></div>
    <div class="contact">
      <div class="contact-row">
        <svg viewBox="0 0 24 24" fill="none" stroke="#fff" stroke-width="2"><path d="M5 3h4l2 5-2.5 1.5a11 11 0 0 0 6 6L16 13l5 2v4a2 2 0 0 1-2 2A16 16 0 0 1 3 5a2 2 0 0 1 2-2z"/></svg>
        <span>858-471-6093</span>
      </div>
      <div class="contact-row">
        <svg viewBox="0 0 24 24" fill="none" stroke="#fff" stroke-width="1.8"><circle cx="12" cy="12" r="9.5"/><path d="M2.5 12h19M12 2.5c3 3 3 16 0 19M12 2.5c-3 3-3 16 0 19M4.5 7h15M4.5 17h15"/></svg>
        <span>www.brightoakbuilders.com</span>
      </div>
    </div>
    <div class="person">
      <div class="person-name">Marcus Delling</div>
      <div class="person-title">Licensed General Contractors</div>
    </div>
    <div class="edge-tab"></div>
  </section>

  <section class="card card--back">
    <div class="brand-name">Harborline Builders</div>
    <div class="divider"></div>
    <div class="services">
      <h2 class="services-title">Our Services</h2>
      <ul class="service-list">
        <li><svg viewBox="0 0 20 20" fill="none" stroke="#fff" stroke-width="2"><circle cx="10" cy="10" r="8"/><path d="M6 10l3 3 5-6"/></svg>Remodel: Kitchen &amp; Bath</li>
        <li><svg viewBox="0 0 20 20" fill="none" stroke="#fff" stroke-width="2"><circle cx="10" cy="10" r="8"/><path d="M6 10l3 3 5-6"/></svg>Painting: Interior &amp; Exterior</li>
        <li><svg viewBox="0 0 20 20" fill="none" stroke="#fff" stroke-width="2"><circle cx="10" cy="10" r="8"/><path d="M6 10l3 3 5-6"/></svg>Flooring: Carpet, Vinyl, Wood</li>
        <li><svg viewBox="0 0 20 20" fill="none" stroke="#fff" stroke-width="2"><circle cx="10" cy="10" r="8"/><path d="M6 10l3 3 5-6"/></svg>Window &amp; Door Replacement</li>
        <li><svg viewBox="0 0 20 20" fill="none" stroke="#fff" stroke-width="2"><circle cx="10" cy="10" r="8"/><path d="M6 10l3 3 5-6"/></svg>Plumbing: Repairs &amp; Upgrades</li>
        <li><svg viewBox="0 0 20 20" fill="none" stroke="#fff" stroke-width="2"><circle cx="10" cy="10" r="8"/><path d="M6 10l3 3 5-6"/></svg>Energy-Efficient Upgrades</li>
        <li><svg viewBox="0 0 20 20" fill="none" stroke="#fff" stroke-width="2"><circle cx="10" cy="10" r="8"/><path d="M6 10l3 3 5-6"/></svg>Deck &amp; Patio Construction</li>
        <li><svg viewBox="0 0 20 20" fill="none" stroke="#fff" stroke-width="2"><circle cx="10" cy="10" r="8"/><path d="M6 10l3 3 5-6"/></svg>Water &amp; Mold Damage</li>
        <li><svg viewBox="0 0 20 20" fill="none" stroke="#fff" stroke-width="2"><circle cx="10" cy="10" r="8"/><path d="M6 10l3 3 5-6"/></svg>Garage Renovation</li>
      </ul>
    </div>
  </section>

</div>
</body>
</html>
```